I need a flyer made , the flyer can be one page or two pages or three pages . I will be posting this on Instagram and social media platforms. I am a luxury home builder , I am looking to hire a construction project manager . Below are some examples and ideas what can be on the flyer

We’re looking for a construction project manager who’s passionate about building luxury homes at the highest standards
We’re hiring construction project manager
* Experience 5+ years in residential project management with a strong portfolio of completed homes.
* location : Bergen County NJ
* excellent leadership skills, leads teams with confidence and clarity
* communicates seamlessly with architects , engineers, designers and clients
*knows how to manage budgets and timelines without compromising quality
*solves problems with a positive solution first mindset
* pays attention to every detail because in luxury the small things are the big things

Apply now , link in bio or DM to connect.

My logo is attached, my web site www.velstridebuilders.com
My style is modern but still warm and inviting. I like a clean classy look .

Please don’t add any images of chairs or people to the flyer , I do not want people on my flyer. Do not add standard images of offices and houses , we are luxury builders , we build homes over 2 million dollars. Keep a classy , simple modern look . High end .

You can add a white hard hat with my logo on it for a image , this is a suggestion does not have to be on my flyer ,

```html
<!DOCTYPE html>
<html lang="en">
<head>
<meta charset="utf-8">
<title>Velstride Builders – We're Hiring</title>
<link href="https://fonts.googleapis.com/css2?family=Poppins:wght@300;400;500;600;800&display=swap" rel="stylesheet">
<style>
  :root {
    --backdrop: #cdd2da;
    --paper: #f1f2f2;
    --paper-clear: rgba(241,242,242,0);
    --ink: #111111;
    --ink-soft: #222222;
    --white: #ffffff;
    --url-grey: #6a6a6a;
    --sky-top: #1b2330;
    --sky-mid: #3a4450;
    --horizon: #c9852f;
    --land: #2b3124;
    --land-deep: #1a1f1c;
    --room-light: #d9dde2;
    --room-warm: #b07a4e;
  }
  * { margin: 0; padding: 0; box-sizing: border-box; }
  html, body { width: 1200px; height: 692px; overflow: hidden; }
  body {
    background: var(--backdrop);
    font-family: "Poppins", sans-serif;
    position: relative;
  }
  .flyer {
    position: absolute;
    top: 115px;
    width: 465px;
    height: 464px;
    background: var(--paper);
    overflow: hidden;
    box-shadow: 0 6px 14px rgba(0,0,0,0.18);
  }
  .flyer--cover { left: 119px; }
  .flyer--details { left: 596px; }

  /* Cover */
  .cover-photo {
    position: absolute; left: 0; top: 0;
    width: 465px; height: 425px;
    background: linear-gradient(180deg,
      var(--sky-top) 0%, var(--sky-mid) 28%, #6b5a43 40%,
      var(--horizon) 47%, #5a4a34 52%, var(--land) 60%, var(--land-deep) 100%);
  }
  .cover-brand {
    position: absolute; right: 0; top: 12px;
    width: 244px; height: 47px;
    background: linear-gradient(90deg, rgba(0,0,0,0) 0%, var(--ink) 30%);
    color: var(--white);
    text-align: right;
    padding-right: 22px;
  }
  .brand-name {
    font-weight: 500;
    letter-spacing: 1px;
    line-height: 1;
  }
  .brand-sub {
    font-weight: 500;
    letter-spacing: 2px;
    font-size: 7px;
    margin-top: 4px;
  }
  .cover-brand .brand-name { font-size: 24px; padding-top: 7px; }
  .cover-brand .brand-sub { margin-right: 42px; }
  .cover-headline {
    position: absolute; left: 42px; top: 104px;
    color: var(--white);
    font-size: 61px;
    line-height: 1;
    letter-spacing: -1.5px;
    white-space: nowrap;
  }
  .cover-headline .light { font-weight: 300; }
  .cover-headline .bold { font-weight: 800; }
  .site-url {
    position: absolute; left: 0; right: 0; top: 436px;
    text-align: center;
    font-size: 12px;
    font-weight: 300;
    letter-spacing: 3.4px;
    color: var(--url-grey);
  }

  /* Details */
  .details-brand {
    position: absolute; left: 0; right: 0; top: 16px;
    text-align: center; color: var(--ink);
  }
  .details-brand .brand-name { font-size: 25px; }
  .details-brand .brand-sub { font-size: 7px; margin-top: 5px; }
  .intro {
    position: absolute; left: 18px; top: 85px; width: 440px;
    font-size: 12.6px; line-height: 15px; color: var(--ink);
  }
  .role-band {
    position: absolute; left: 0; top: 126px;
    width: 465px; height: 22px;
    background: linear-gradient(90deg, var(--ink) 0%, var(--ink) 55%, rgba(0,0,0,0.25) 92%, rgba(0,0,0,0) 100%);
    color: var(--white);
    font-size: 14px; font-weight: 500;
    line-height: 22px;
    padding-left: 17px;
  }
  .requirements {
    position: absolute; left: 0; top: 165px;
    list-style: none;
    z-index: 2;
  }
  .requirements li {
    display: flex; align-items: center;
    height: 18.5px;
    font-size: 8px; color: var(--ink-soft);
    white-space: nowrap;
  }
  .requirements li::before {
    content: "";
    width: 26px; height: 7px;
    background: var(--ink);
    margin-right: 4px;
    flex: none;
  }
  .interior-sketch {
    position: absolute; left: 202px; top: 279px;
    width: 263px; height: 185px;
    z-index: 1;
    background:
      linear-gradient(90deg, var(--paper) 0%, var(--paper-clear) 35%),
      linear-gradient(180deg, var(--paper) 0%, var(--paper-clear) 30%),
      linear-gradient(160deg, var(--room-light) 20%, #a9b3bd 55%, var(--room-warm) 85%, #8a6648 100%);
  }
  .apply-cta {
    position: absolute; left: 0; top: 333px;
    width: 218px; height: 34px;
    color: var(--white);
    padding: 5px 0 0 18px;
    z-index: 2;
  }
  .apply-cta svg { position: absolute; left: 0; top: 0; }
  .apply-cta p { position: relative; line-height: 11px; }
  .apply-cta .apply-title { font-size: 11px; font-weight: 800; }
  .apply-cta .apply-sub { font-size: 10px; font-weight: 400; }
  .flyer--details .site-url { z-index: 2; }
</style>
</head>
<body>

  <section class="flyer flyer--cover">
    <div class="cover-photo" role="img" aria-label="Aerial photo at dusk of a terraced luxury residence overlooking a bay and city skyline"></div>
    <div class="cover-brand">
      <div class="brand-name">VELSTRIDE</div>
      <div class="brand-sub">builders</div>
    </div>
    <h1 class="cover-headline"><span class="light">WE’RE </span><span class="bold">HIRING</span></h1>
    <p class="site-url">www.velstridebuilders.com</p>
  </section>

  <section class="flyer flyer--details">
    <div class="details-brand">
      <div class="brand-name">VELSTRIDE</div>
      <div class="brand-sub">builders</div>
    </div>
    <p class="intro">We’re looking for a construction project manager who’s passionate about building luxury homes at the highest standards</p>
    <h2 class="role-band">WE’RE HIRING CONSTRUCTION PROJECT MANAGER</h2>
    <ul class="requirements">
      <li>Experience 5+ years in residential project management with a strong portfolio of completed homes</li>
      <li>Location : Bergen County NJ</li>
      <li>Excellent leadership skills, leads teams with confidence and clarity</li>
      <li>Communicates seamlessly with architects, engineers, designers and clients</li>
      <li>Knows how to manage budgets and timelines without compromising quality</li>
      <li>Solves problems with a positive solution first mindset</li>
      <li>Pays attention to every detail because in luxury the small things are the big things</li>
    </ul>
    <div class="interior-sketch" role="img" aria-label="Half-sketched, half-rendered luxury penthouse living room with city views being drawn with a pen"></div>
    <div class="apply-cta">
      <svg width="218" height="34" viewBox="0 0 218 34" aria-hidden="true"><polygon points="0,0 184,0 218,34 0,34" fill="#111111"/></svg>
      <p class="apply-title">APPLY NOW,</p>
      <p class="apply-sub">LINK IN BIO OR DM TO CONNECT</p>
    </div>
    <p class="site-url">www.velstridebuilders.com</p>
  </section>

</body>
</html>
```